NZ First of it's kind solutions directory and marketplace for busy Mums needs a business card design

We need a business card design for our new nationwide business in NZ (long term plans to go global). We provide solutions to the everyday challenges that busy Mums face by connecting them with quality communities and suppliers of carefully selected, relevant products and services. We sell direct via our online marketplace. The final design should communicate our values of inclusivity, quality and smart solutions. Colours should incorporate our logo colour palette of #477077 and #6ba8b2. Our website is at https://www.brightnestmums.example

Target Market(s)

busy Mums, Age 28 – 50, female, income over $100K, location main centres NZ primarily but NZ wide. Is likely juggling work or career with a young family. Probably had hobbies which have fallen by the wayside.
-Wants to succeed in her chosen career without compromising on family life
-to successfully juggle her career without feeling like she is compromising her children
- Is time poor, something always has to give and it’s generally her health (she’ll stay up late, get stressed)
- probably ex corporate or professional career. Has discretional income

Industry/Entity Type

Business

Contact Information for Business Card

Lena Forbisher, Founder, BrightNestMums.example (Strapline Tap; Gather; Sorted), 47 Kowhai Terrace, Ellerslie, Auckland 1051, New Zealand. Mob: 021 483 517 Ph: +64 (0)9 571 4860

Font styles to use
Other font styles liked:
• Raleway, and/or Architects Daughter

Colors
00a990
33b8a4
86cfc6
cfeae6

Requirements
Must have
• the above details, streamline. the logo and colours associated with those logos
Should not have
• foil or metallic colours

```html
<!DOCTYPE html>
<html lang="en">
<head>
<meta charset="utf-8">
<title>BrightNestMums Business Card</title>
<link rel="stylesheet" href="https://fonts.googleapis.com/css2?family=Rubik:wght@400;500&family=Work+Sans:wght@400&display=swap">
<style>
  :root {
    --teal-deep: #477077;
    --teal-light: #6ba8b2;
    --ink: #3f5f65;
    --paper: #ffffff;
    --backdrop: #dedede;
  }
  * { margin: 0; padding: 0; box-sizing: border-box; }
  html, body {
    width: 1200px; height: 897px; overflow: hidden;
    background: var(--backdrop);
  }
  .sheet { position: relative; width: 1200px; height: 897px; }
  .card {
    position: absolute; left: 303px; width: 594px; height: 339px;
  }
  .card--front {
    top: 92px; background: var(--paper);
  }
  .card--back {
    top: 469px; background: var(--teal-deep);
  }
  .brand {
    position: absolute; display: flex; align-items: center; gap: 10px;
    font-family: "Rubik", sans-serif; font-weight: 500; letter-spacing: -0.5px;
  }
  .brand__dot { border-radius: 50%; flex: none; }
  .card--front .brand {
    right: 28px; top: 52px; font-size: 30px; color: var(--teal-deep);
  }
  .card--front .brand__dot { width: 26px; height: 26px; background: var(--teal-deep); }
  .card--back .brand {
    left: 50%; top: 142px; transform: translateX(-50%);
    font-size: 40px; color: var(--paper); white-space: nowrap;
  }
  .card--back .brand__dot { width: 36px; height: 36px; background: var(--paper); }
  .holder { position: absolute; left: 32px; top: 180px; }
  .holder__name {
    font-family: "Rubik", sans-serif; font-weight: 400;
    font-size: 29px; color: var(--teal-light); line-height: 1.1;
  }
  .holder__role {
    font-family: "Work Sans", sans-serif; font-size: 14px;
    color: var(--ink); letter-spacing: 0.6px; margin-top: 1px;
  }
  .rule {
    position: absolute; left: 32px; right: 28px; top: 247px;
    height: 1px; background: var(--teal-deep);
  }
  .contacts {
    position: absolute; left: 32px; top: 264px;
    font-family: "Work Sans", sans-serif; font-size: 13.4px;
    color: var(--ink); letter-spacing: 0.4px; line-height: 22px;
    white-space: nowrap;
  }
  .contacts__label { color: var(--teal-light); }
  .card--back .web {
    position: absolute; left: 0; right: 0; top: 298px; text-align: center;
    font-family: "Work Sans", sans-serif; font-size: 14.5px;
    letter-spacing: 1px; color: var(--paper);
  }
</style>
</head>
<body>
<main class="sheet">
  <section class="card card--front">
    <div class="brand"><span class="brand__dot"></span>BrightNestMums</div>
    <div class="holder">
      <p class="holder__name">Lena Forbisher</p>
      <p class="holder__role">Founder</p>
    </div>
    <div class="rule"></div>
    <div class="contacts">
      <p><span class="contacts__label">M :</span> 021 483 517 | <span class="contacts__label">P :</span> +64 (0)9 571 4860 | <span class="contacts__label">W :</span> www.brightnestmums.example</p>
      <p><span class="contacts__label">A :</span> 47 Kowhai Terrace, Ellerslie Auckland 1051, New Zealand</p>
    </div>
  </section>
  <section class="card card--back">
    <div class="brand"><span class="brand__dot"></span>BrightNestMums</div>
    <p class="web">www.brightnestmums.example</p>
  </section>
</main>
</body>
</html>
```